Business Card Design Project

Business Card
We are rebranding with a new logo
Industry/Entity Type
Business
Contact Information for Business Card
Dennis Morvale +61 487215963 dennis@quorv.com.au P.O. Box 872 Fernlow QLD 4309
Requirements
Must have
- Logo

```html
<!DOCTYPE html>
<html lang="en">
<head>
<meta charset="utf-8">
<title>Quorv International – Business Card</title>
<link rel="stylesheet" href="https://fonts.googleapis.com/css2?family=Roboto:wght@400;500;700&family=Roboto+Condensed:wght@700&display=swap">
<style>
  :root {
    --backdrop: #2b2b2b;
    --card-white: #f4f4f4;
    --brand-blue: #1a8cc0;
    --brand-blue-dark: #0e5f86;
    --brand-orange: #ec8a1f;
    --text-grey: #4a4a4a;
    --rule-grey: #b5b5b5;
    --white: #ffffff;
  }
  * { margin: 0; padding: 0; box-sizing: border-box; }
  html, body { width: 1200px; height: 960px; overflow: hidden; }
  body {
    background: var(--backdrop);
    font-family: "Roboto", Arial, sans-serif;
    position: relative;
  }
  .card {
    position: absolute;
    width: 600px;
    height: 343px;
    overflow: hidden;
  }
  .card-front { left: 314px; top: 113px; background: var(--card-white); }
  .card-back  { left: 311px; top: 472px; background: var(--brand-orange); }

  .wordmark {
    position: absolute;
    font-family: "Roboto", Arial, sans-serif;
    font-weight: 700;
    line-height: 1;
  }
  .wordmark-name { display: block; font-size: 60px; letter-spacing: 1px; }
  .wordmark-tag { display: block; font-size: 16px; letter-spacing: 3px; text-transform: uppercase; margin-top: 8px; }
  .card-front .wordmark { right: 40px; top: 52px; text-align: right; color: var(--brand-blue); }
  .card-back .wordmark { left: 0; right: 0; top: 118px; text-align: center; color: var(--white); }

  .holder-name {
    position: absolute; left: 36px; top: 206px;
    font-family: "Roboto Condensed", Arial, sans-serif;
    font-weight: 700; font-size: 21px; color: var(--brand-blue);
    text-transform: uppercase;
  }
  .divider {
    position: absolute; left: 36px; right: 38px; top: 239px;
    height: 1px; background: var(--rule-grey);
  }
  .contact-list {
    position: absolute; left: 36px; top: 250px;
    list-style: none; font-size: 14px; color: var(--text-grey); line-height: 19px;
  }
  .contact-list li { display: flex; align-items: center; gap: 8px; }
  .contact-list svg { width: 14px; height: 14px; fill: var(--brand-blue); }
  .postal-address {
    position: absolute; right: 36px; top: 250px;
    font-style: normal; font-size: 14px; color: var(--text-grey);
    line-height: 19px; text-align: right;
  }
  .front-band { position: absolute; left: 0; bottom: 0; width: 600px; height: 40px; }
  .front-web {
    position: absolute; right: 34px; top: 315px;
    font-size: 14px; letter-spacing: 2.4px; color: var(--white);
  }
  .back-web {
    position: absolute; left: 0; right: 0; top: 300px; text-align: center;
    font-size: 14px; letter-spacing: 6px; color: var(--white);
  }
</style>
</head>
<body>
  <section class="card card-front">
    <div class="wordmark">
      <span class="wordmark-name">Quorv</span>
      <span class="wordmark-tag">International</span>
    </div>

    <h1 class="holder-name">Dennis Morvale</h1>
    <div class="divider"></div>

    <ul class="contact-list">
      <li>
        <svg viewBox="0 0 24 24" aria-hidden="true"><path d="M6.6 10.8a15.1 15.1 0 0 0 6.6 6.6l2.2-2.2c.3-.3.7-.4 1-.2 1.1.4 2.3.6 3.6.6.6 0 1 .4 1 1V20c0 .6-.4 1-1 1A17 17 0 0 1 3 4c0-.6.4-1 1-1h3.5c.6 0 1 .4 1 1 0 1.3.2 2.5.6 3.6.1.3 0 .7-.2 1z"/></svg>
        <span>+61 487215963</span>
      </li>
      <li>
        <svg viewBox="0 0 24 24" aria-hidden="true"><path d="M2 5h20v14H2z M3 6l9 7 9-7" stroke="#f4f4f4" stroke-width="1.5"/></svg>
        <span>dennis@quorv.com.au</span>
      </li>
    </ul>

    <address class="postal-address">P.O. Box 872<br>Fernlow QLD 4309</address>

    <svg class="front-band" viewBox="0 0 600 40" aria-hidden="true">
      <defs>
        <linearGradient id="band-blue" x1="0" x2="1" y1="0" y2="0">
          <stop offset="0" stop-color="var(--brand-blue-dark)"/>
          <stop offset="0.55" stop-color="var(--brand-blue)"/>
          <stop offset="1" stop-color="var(--brand-blue-dark)"/>
        </linearGradient>
      </defs>
      <path d="M0 17 H350 C356 17 358 27 350 27 H0 Z" fill="var(--brand-orange)"/>
      <path d="M0 28 H346 C362 28 362 4 384 4 H600 V40 H0 Z" fill="url(#band-blue)"/>
    </svg>
    <div class="front-web">www.quorv.com.au</div>
  </section>

  <section class="card card-back">
    <div class="wordmark">
      <span class="wordmark-name">Quorv</span>
      <span class="wordmark-tag">International</span>
    </div>
    <div class="back-web">www.quorv.com.au</div>
  </section>
</body>
</html>
```